Real Estate Company Looking for Business Card Designs for 3 Executives

Hello!
Thanks so much for considering our project! We are a real estate investment company located in Edmonton, Alberta called Bellhaven Group of Companies. We invest/develop both commercial and residential real estate and are looking to create 3 DOUBLE-SIDED business cards for 3 top executives in the company! (for some reason it won't let us select the double-sided option, but yes, the cards are double sided and would be happy to tip extra)

We have certain guidelines that we want our business cards to for sure follow - the back of the Business card has to be the Black Background Version of the Logo which has already been designed and linked as a file (first file). We want the entire back of the card to simply just be the black background logo. In terms of the front of the card, would like to see a smaller version of the white background logo (linked as the second file) in the top left hand corner - of course, feel free to get creative and we can make revisions together along the way! and Then after that, just text. We want the card to be sharp, clean, easy on the eyes and highly professional looking. We would like the card to include the Full name of the Company (Bellhaven Group of Companies), Name of the Person, Title, Phone, Email. If possible please provide the front part of the card for 3 people:

1) Bellhaven Group of Companies, Liora Quenby, Chief Financial Officer, 780-555-0142, lioraquenby@bellhavengroup.example

2) Bellhaven Group of Companies, Tobias Quenby, Chief Executive Officer, 780-555-0187, tobiasquenby@bellhavengroup.example

3) Bellhaven Group of Companies, Rui Delcourt, Chief Operations Officer, 587-555-0163, ruidelcourt@bellhavengroup.example

Thank you so much for considering our project & we look forward to seeing your designs!

```html
<!DOCTYPE html>
<html lang="en">
<head>
<meta charset="utf-8">
<title>Bellhaven Group of Companies — Business Card</title>
<link rel="stylesheet" href="https://fonts.googleapis.com/css2?family=Karla:wght@400;700&display=swap">
<style>
  :root {
    --stage: #1b1b1c;
    --card-dark: #3a3a3b;
    --logo-tone: #8d8d8f;
    --card-light: #ffffff;
    --ink: #111111;
    --ink-soft: #555555;
    --rule: #222222;
  }
  * { box-sizing: border-box; margin: 0; padding: 0; }
  html, body {
    width: 1200px; height: 874px; overflow: hidden;
    background: var(--stage);
    font-family: "Karla", Arial, sans-serif;
  }
  .stage {
    position: relative; width: 1200px; height: 874px;
  }
  .card {
    position: absolute; left: 280px; width: 640px; height: 366px;
  }
  .card-back { top: 66px; background: var(--card-dark); }
  .card-front { top: 442px; background: var(--card-light); color: var(--ink); }

  .brand-mark {
    position: absolute; inset: 0;
    display: flex; align-items: center; justify-content: center; gap: 18px;
  }
  .brand-square { width: 22px; height: 22px; background: var(--logo-tone); }
  .brand-name {
    font-size: 40px; font-weight: 400; letter-spacing: 12px;
    color: var(--logo-tone);
  }

  .identity {
    position: absolute; top: 150px; right: 392px; text-align: right;
  }
  .person-name {
    font-size: 24px; font-weight: 700; letter-spacing: 1px; line-height: 1.1;
  }
  .person-title {
    font-size: 14px; color: var(--ink-soft); margin-top: 2px;
  }
  .divider {
    position: absolute; left: 262px; top: 144px; width: 1px; height: 70px;
    background: var(--rule);
  }
  .contacts {
    position: absolute; left: 276px; top: 146px; list-style: none;
    font-size: 14px; line-height: 22px; color: var(--ink);
  }
  .contacts li { display: flex; align-items: center; gap: 7px; }
  .contacts svg { width: 13px; height: 13px; flex: none; }
  .company {
    position: absolute; left: 180px; top: 280px;
    font-size: 14px; font-weight: 700; letter-spacing: 0.6px; text-transform: uppercase;
  }
</style>
</head>
<body>
<main class="stage">
  <section class="card card-back" aria-label="Card back">
    <div class="brand-mark">
      <span class="brand-square"></span>
      <span class="brand-name">BELLHAVEN</span>
    </div>
  </section>

  <section class="card card-front" aria-label="Card front">
    <div class="identity">
      <h1 class="person-name">LIORA QUENBY</h1>
      <p class="person-title">Chief Financial Officer</p>
    </div>
    <div class="divider"></div>
    <ul class="contacts">
      <li>
        <svg viewBox="0 0 16 16" aria-hidden="true"><circle cx="8" cy="8" r="8" fill="#111"/><path d="M5 4.5l1.5-.5 1 2-1 .8c.4 1 1.2 1.8 2.2 2.2l.8-1 2 1-.5 1.5c-3 .2-6.2-3-6-6z" fill="#fff"/></svg>
        780-555-0142
      </li>
      <li>
        <svg viewBox="0 0 16 16" aria-hidden="true"><circle cx="8" cy="8" r="8" fill="#111"/><rect x="4" y="5.2" width="8" height="5.6" fill="#fff"/><path d="M4 5.4l4 3 4-3" stroke="#111" stroke-width="1" fill="none"/></svg>
        lioraquenby@bellhavengroup.example
      </li>
      <li>
        <svg viewBox="0 0 16 16" aria-hidden="true"><circle cx="8" cy="8" r="8" fill="#111"/><circle cx="8" cy="8" r="4" fill="none" stroke="#fff" stroke-width="1.2"/><path d="M4 8h8M8 4c-1.6 2.4-1.6 5.6 0 8M8 4c1.6 2.4 1.6 5.6 0 8" stroke="#fff" stroke-width="0.9" fill="none"/></svg>
        www.bellhavengroup.example
      </li>
    </ul>
    <p class="company">Bellhaven Group of Companies</p>
  </section>
</main>
</body>
</html>
```